Exciting letterhead design for startup company

We need a A4 letterhead designing.

See attached file which contains the logo (on 3 different coloured backgrounds) and then the address and contact information. It also contains 4 colours that can be used.

Looking for an imaginative design. We are a young, fresh startup website design company so need a letterhead that reflects our industry.

Sans Serif

```html
<!DOCTYPE html>
<html lang="en">
<head>
<meta charset="utf-8">
<title>PageLoom Letterhead</title>
<link rel="stylesheet" href="https://fonts.googleapis.com/css2?family=Open+Sans:wght@400;600;700&display=swap">
<style>
  :root {
    --backdrop: #e0e0e0;
    --paper: #ffffff;
    --ink: #231f20;
    --ink-soft: #3a3a3a;
    --brand-blue: #0095da;
  }
  * { box-sizing: border-box; margin: 0; padding: 0; }
  html, body {
    width: 1200px;
    height: 1200px;
    overflow: hidden;
    background: var(--backdrop);
    font-family: "Open Sans", Arial, sans-serif;
    color: var(--ink);
  }
  .letterhead {
    position: absolute;
    left: 273px;
    top: 138px;
    width: 654px;
    height: 924px;
    background: var(--paper);
  }
  .brand-name {
    position: absolute;
    left: 38px;
    top: 44px;
    font-size: 42px;
    font-weight: 600;
    letter-spacing: -1.5px;
    line-height: 1;
    color: var(--ink);
  }
  .contact-line {
    position: absolute;
    left: 37px;
    top: 107px;
    display: flex;
    align-items: center;
    gap: 6px;
    font-size: 10.5px;
    color: var(--ink-soft);
  }
  .contact-line svg { display: block; }
  .contact-line .item { display: flex; align-items: center; gap: 6px; }
  .contact-line .item + .item { margin-left: 2px; }
  .company-details {
    position: absolute;
    right: 37px;
    top: 44px;
    text-align: right;
    font-style: normal;
    font-size: 8.6px;
    line-height: 12px;
    color: var(--ink-soft);
  }
  .company-details .company-name {
    font-size: 15.5px;
    font-weight: 700;
    line-height: 20px;
    color: var(--ink);
    margin-bottom: 1px;
  }
  .footer-band {
    position: absolute;
    left: 0;
    bottom: 0;
    width: 100%;
    height: 14px;
    background: var(--brand-blue);
  }
</style>
</head>
<body>
  <main class="letterhead">
    <header>
      <div class="brand-name">PageLoom</div>
      <div class="contact-line">
        <span class="item">
          <svg width="11" height="9" viewBox="0 0 11 9" aria-hidden="true">
            <path d="M1 3 C1 1 10 1 10 3 L8.5 3.8 L7.5 2.6 L3.5 2.6 L2.5 3.8 Z M2.5 4.5 L4 3.4 L7 3.4 L8.5 4.5 L8.5 8 L2.5 8 Z" fill="var(--brand-blue)"/>
          </svg>
          0845 000 1234
        </span>
        <span class="item">
          <svg width="11" height="8" viewBox="0 0 11 8" aria-hidden="true">
            <rect x="0.5" y="0.5" width="10" height="7" fill="var(--brand-blue)"/>
            <path d="M0.8 0.8 L5.5 4.6 L10.2 0.8" fill="none" stroke="#fff" stroke-width="1"/>
          </svg>
          hello@pageloom.co.uk
        </span>
      </div>
      <address class="company-details">
        <div class="company-name">PageLoom Limited</div>
        Suite 4, Harbour Court, Leeds LS1 4AB.<br>
        Registered in England &amp; Wales<br>
        Company No 01234567
      </address>
    </header>
    <div class="footer-band" aria-hidden="true"></div>
  </main>
</body>
</html>
```